Buch-/eBook-Cover für Sachbuch gesucht
Zielgruppe
We're selfpublishing nonfiction books. Interested are adults - mostly man (age range: 25-50) - who want to learn more about leadership at their workplaces.
Aufgabenstellung
The design should be clean and simple, title easy to read, good color contrast (the cover has to stand out from an white background).

```html
<!DOCTYPE html>
<html lang="en">
<head>
<meta charset="utf-8">
<title>Leadership – Book Cover</title>
<link rel="stylesheet" href="https://fonts.googleapis.com/css2?family=Bebas+Neue&family=Roboto:wght@400&family=Roboto+Condensed:wght@400&display=swap">
<style>
  :root {
    --navy: #0c1445;
    --green: #4aea26;
    --white: #f6f6f8;
    --slate: #3f4770;
    --slate-dark: #232a58;
  }
  html, body {
    margin: 0;
    padding: 0;
    overflow: hidden;
    background: var(--navy);
  }
  .cover {
    display: block;
    width: 750px;
    height: 1200px;
  }
  .cover__bg { fill: var(--navy); }
  .cover__decor { fill: url(#decorTone); }
  .author {
    font-family: "Roboto", sans-serif;
    font-size: 42px;
    fill: var(--white);
  }
  .title {
    font-family: "Bebas Neue", sans-serif;
    font-size: 268px;
    fill: var(--green);
  }
  .subtitle {
    font-family: "Roboto Condensed", sans-serif;
    font-size: 55px;
    fill: var(--white);
  }
</style>
</head>
<body>
<svg class="cover" viewBox="0 0 750 1200" width="750" height="1200" xmlns="http://www.w3.org/2000/svg">
  <defs>
    <linearGradient id="decorTone" x1="0" y1="0" x2="0.3" y2="1">
      <stop offset="0" stop-color="#0c1445" stop-opacity="0"/>
      <stop offset="0.35" stop-color="#232a58"/>
      <stop offset="1" stop-color="#3f4770"/>
    </linearGradient>
  </defs>

  <rect class="cover__bg" width="750" height="1200"/>
  <rect class="cover__decor" x="0" y="620" width="750" height="580"
        role="img" aria-label="Abstract geometric background of overlapping diagonal bands in navy and slate tones"/>

  <text class="author" x="356" y="82" text-anchor="middle">Daniel Whitmore</text>

  <g class="title">
    <text x="40" y="344" textLength="682" lengthAdjust="spacingAndGlyphs">LEADER</text>
    <text x="34" y="600" textLength="408" lengthAdjust="spacingAndGlyphs">SHIP</text>
  </g>

  <g class="subtitle">
    <text x="477" y="432">Fostering</text>
    <text x="477" y="487">Growth and</text>
    <text x="477" y="542">Inspiring</text>
    <text x="477" y="597">Excellence</text>
  </g>
</svg>
</body>
</html>
```